New Fun, Positive, energised looking Business Card Needed for High Achiever Coach

I am looking for a two sided full colour business card. I am self employed and have recently re branded my 1-2-1 work re-vitalising high achievers. My target client base for these cards is therefore high achievers - usually aged 40 -55, they are often entrepreneurs, CEO or work in banking and finance and 2/3 are male. I work with them on 90 day or 6 month coaching programs to help them live their success in a healthier, more sustainable and fulfiiled way. They pay for this privately so though they are corporate types the cards need not look 'corporate'. I want to portray the idea of transformation, vitality and re-connecting.
You can get a feel for the look I like on my new website: morvenlisk.co.uk
I want to use this logo with strapline (Re-Vitalising High Achievers) (I purchased off Logoharbor) and font/ colours (the turquoise and green).
Details to include on the card:
www.morvenlisk.co.uk
+44 7915 302618
morven@morvenlisk.co.uk
skype: morvenlisk
I'd also like to include:
Do you struggle to switch off? Want to be healthier and feel fitter? Want closer relationships? More clarity over the direction you are headed? I can help you do these things using integrated mind-body techniques. Visit morvenlisk.co.uk TODAY to apply for a FREE Breakthrough session.
BUT if that is too much text for a card I am open to advice/ammendments.
Updates
Thanks for your design - I am considering them. PLease change the wording to :

```html
<!DOCTYPE html>
<html lang="en">
<head>
<meta charset="utf-8">
<title>Morven Lisk – Business Card</title>
<link rel="stylesheet" href="https://fonts.googleapis.com/css2?family=Open+Sans:wght@400;600;700;800&display=swap">
<style>
  :root {
    --turquoise: #0aa5c8;
    --turquoise-deep: #0897b8;
    --green: #5cb85c;
    --ink: #2f3033;
    --paper: #ffffff;
    --backdrop: #e9eaec;
    --divider: #b9bcc0;
  }
  * { margin: 0; padding: 0; box-sizing: border-box; }
  html, body {
    width: 1200px; height: 987px; overflow: hidden;
    background: var(--backdrop);
    font-family: "Open Sans", Arial, sans-serif;
  }
  .canvas {
    position: relative; width: 1200px; height: 987px;
  }
  .card {
    position: absolute; left: 215px; width: 770px; height: 440px;
    border-radius: 40px; overflow: hidden;
    box-shadow: 0 6px 18px rgba(0,0,0,0.12);
  }
  .card--front { top: 36px; background: var(--paper); }
  .card--back  { top: 510px; background: var(--turquoise); }

  .front-wave { position: absolute; inset: 0; }
  .website {
    position: absolute; left: 44px; top: 352px;
    color: var(--paper); font-weight: 600; font-size: 25px; letter-spacing: 1.5px;
  }

  .brand {
    position: absolute; left: 70px; top: 120px; width: 270px;
    display: flex; flex-direction: column; align-items: center; gap: 14px;
  }
  .brand__dot {
    width: 64px; height: 64px; border-radius: 50%; background: var(--green);
  }
  .brand__name {
    color: var(--turquoise); font-weight: 800; font-size: 36px; letter-spacing: 0.5px;
  }

  .divider {
    position: absolute; left: 372px; top: 110px; width: 2px; height: 190px;
    background: linear-gradient(to bottom, transparent, var(--divider) 35%, var(--divider) 65%, transparent);
  }

  .contacts {
    position: absolute; left: 400px; top: 150px; list-style: none;
    display: flex; flex-direction: column; gap: 16px;
  }
  .contacts__item {
    display: flex; align-items: center; gap: 12px;
    color: var(--ink); font-size: 24px; font-weight: 400;
  }
  .contacts__icon { width: 22px; height: 22px; flex: none; }

  .pitch {
    position: absolute; inset: 0;
    display: flex; flex-direction: column; justify-content: center; align-items: center;
    color: var(--paper); text-align: center;
    font-size: 25px; font-weight: 600; line-height: 1.3;
  }
  .pitch strong { font-weight: 800; }
</style>
</head>
<body>
<main class="canvas">

  <section class="card card--front" aria-label="Card front">
    <svg class="front-wave" viewBox="0 0 770 440" width="770" height="440" aria-hidden="true">
      <path d="M0 286 C 190 270, 360 420, 770 392" fill="none" stroke="var(--green)" stroke-width="7"/>
      <path d="M0 298 C 190 282, 360 432, 770 404 L770 440 L0 440 Z" fill="var(--turquoise)"/>
    </svg>
    <p class="website">www.morvenlisk.co.uk</p>

    <div class="brand">
      <span class="brand__dot"></span>
      <span class="brand__name">Morven Lisk</span>
    </div>

    <span class="divider"></span>

    <ul class="contacts">
      <li class="contacts__item">
        <svg class="contacts__icon" viewBox="0 0 24 24" aria-hidden="true">
          <circle cx="12" cy="12" r="11" fill="var(--turquoise)"/>
          <path d="M8 6.5c-.8.5-1.3 1.4-1 2.6.8 3.4 3.6 6.4 7 7.6 1.2.4 2.2 0 2.8-.8l-2.3-2.1-1.4.8c-1.5-.8-2.7-2-3.5-3.5l.9-1.3z" fill="var(--paper)"/>
        </svg>
        +44 7915 302618
      </li>
      <li class="contacts__item">
        <svg class="contacts__icon" viewBox="0 0 24 24" aria-hidden="true">
          <rect x="1" y="5" width="22" height="15" rx="2" fill="var(--turquoise)"/>
          <path d="M2 6.5l10 7 10-7" fill="none" stroke="var(--paper)" stroke-width="2"/>
        </svg>
        morven@morvenlisk.co.uk
      </li>
      <li class="contacts__item">
        <svg class="contacts__icon" viewBox="0 0 24 24" aria-hidden="true">
          <rect x="1" y="1" width="22" height="22" rx="5" fill="var(--turquoise)"/>
        </svg>
        morvenlisk
      </li>
    </ul>
  </section>

  <section class="card card--back" aria-label="Card back">
    <div class="pitch">
      <p>Do you struggle to switch off?</p>
      <p>Want to be healthier and feel fitter?</p>
      <p>Want closer relationships?</p>
      <p>More clarity over the direction you are headed?</p>
      <p>I can help you do these things using integrated</p>
      <p>mind-body techniques.</p>
      <p>Visit <strong>morvenlisk.co.uk</strong> TODAY to apply for a</p>
      <p>FREE Breakthrough session.</p>
    </div>
  </section>

</main>
</body>
</html>
```